eCommerce website for a DIY shop & communal center

We need a website for a business called The Maple Bench. The Maple Bench is both a shop and communal establishment where people with shared interests, especially in DIY (Do It Yourself) and crafting, can gather to shop for & work on projects while sharing ideas, equipment, supplies and knowledge. The shop is both brick & motor and online. The physical communal space provides workstations, equipment, tools and supplies and expertise for DIY lovers to create their projects.

Target Market(s)

Middle & upper class DIY enthusiasts, creative hobbyists, budding artists & small business owners

Industry/Entity Type

DIY, Arts & Crafts

Coding

Coded - Design and coding required

Number of Pages Required

5+ page

Requirements
Must have
• Menus to include 1. home page (with about us, operating hours, contacts, location, meet the team); 2. Bench activities (how to DIY at the Bench, booking, equipment & tools, house rules); 3. Bench events (events in the Bench, offsite events); 4. Resources (FAQs, tutorials, blogs, eBooks) and 5. Online shop
Nice to have
• Branding guidelines eg logo colours (see attachment) to influence design. Tillpost shop. Booking feature for activities & events at the Bench.

```html
<!DOCTYPE html>
<html lang="en">
<head>
<meta charset="utf-8">
<title>Resources – The Maple Bench</title>
<link href="https://fonts.googleapis.com/css2?family=Roboto:wght@400;500;700&family=Great+Vibes&display=swap" rel="stylesheet">
<style>
:root{
  --ink:#1c1c1c;
  --muted:#6b6b6b;
  --line:#d9d9d9;
  --orange:#f47c3c;
  --blue:#2f98d4;
  --navy:#2b2a66;
  --soft:#f7f7f7;
  --black:#050505;
  --white:#ffffff;
  --coral:#f46b6b;
}
*{box-sizing:border-box;margin:0;padding:0}
html,body{width:1200px;height:3686px;overflow:hidden}
body{position:relative;font-family:'Roboto',sans-serif;color:var(--ink);background:var(--white)}
.abs{position:absolute}
.script{font-family:'Great Vibes',cursive;font-weight:400;font-size:50px;text-align:center;left:0;width:1200px}
.script .o{color:var(--orange)} .script .b{color:var(--blue)}
.intro{left:0;width:1200px;text-align:center;font-size:14.5px;line-height:25px;color:#555}

/* header */
.topbar{top:0;left:0;width:1200px;height:50px;border-bottom:1px solid #e6e6e6}
.phone-ico{left:101px;top:5px;width:38px;height:38px;border:1.5px solid #999;border-radius:50%;display:flex;align-items:center;justify-content:center}
.phone-num{left:149px;top:14px;font-size:15px;font-weight:500}
.social-top{top:5px;width:37px;height:37px;border:1.5px solid #999;border-radius:50%}
.nav{top:63px;font-size:15px;font-weight:500;letter-spacing:.2px}
.logo-disc{left:524px;top:-20px;width:152px;height:153px;border-radius:50%;background:var(--white);border:1px solid #e6e6e6;display:flex;align-items:center;justify-content:center;text-align:center}
.logo-disc span{font-size:19px;font-weight:700;color:var(--orange);line-height:23px;margin-top:24px}
.hero{top:100px;left:0;width:1200px;height:296px;background:linear-gradient(100deg,#4a3a2e 0%,#6d5240 40%,#8a4a3c 60%,#5a4536 100%)}
.hero h1{position:absolute;left:103px;top:84px;font-size:55px;font-weight:700;color:var(--white)}

/* faq */
.faq{left:210px;width:779px;height:57px;border:1px solid var(--line);background:var(--white)}
.faq span{position:absolute;left:22px;top:17px;font-size:19px;font-weight:500}
.faq svg{position:absolute;right:10px;top:17px}

/* blog */
.blog-band{top:1139px;left:0;width:1200px;height:1194px;background:var(--soft)}
.kicker{font-size:14.5px;color:var(--navy);font-weight:500}
.post-title{font-size:22px;font-weight:500;line-height:34px}
.post-text{font-size:13.5px;line-height:24px;color:#777}

/* books */
.book{top:2571px;width:236px;height:287px;background:linear-gradient(90deg,#e25a5a 0,#f46b6b 6%,#f47070 100%)}
.book-name{top:2875px;font-size:24px;font-weight:500}
.book-sub{top:2905px;font-size:17.5px;color:#555}

/* indemnity */
.indemnity{top:3016px;left:0;width:1200px;height:290px;background:var(--blue)}
.btn{left:451px;top:3201px;width:299px;height:46px;border-radius:23px;background:var(--orange);color:var(--white);font-size:14px;font-weight:700;display:flex;align-items:center;justify-content:center;letter-spacing:.3px}

/* footer */
.footer{top:3306px;left:0;width:1200px;height:380px;background:var(--black)}
.f-head{top:3385px;color:var(--white);font-size:16.5px;font-weight:700}
.f-list{top:3419px;color:var(--white);font-size:14px;line-height:28.3px;list-style:none}
.email{left:843px;top:3417px;width:256px;height:40px;border-radius:20px;background:var(--white);font-size:13px;padding:13px 0 0 15px;color:#222}
.subscribe{left:843px;top:3467px;width:256px;height:42px;border-radius:21px;background:var(--orange);color:var(--white);font-size:14px;font-weight:700;display:flex;align-items:center;justify-content:center}
.f-social{top:3530px;width:34px;height:34px;border-radius:50%;background:var(--white)}
.rule{left:101px;top:3600px;width:998px;height:1px;background:#2a2a2a}
.copy{top:3617px;left:0;width:1200px;text-align:center;color:var(--white);font-size:13px}
</style>
</head>
<body>

<div class="abs topbar"></div>
<div class="abs phone-ico">
  <svg width="18" height="18" viewBox="0 0 24 24"><path d="M6.6 10.8a15.1 15.1 0 0 0 6.6 6.6l2.2-2.2c.3-.3.7-.4 1-.2 1.1.4 2.3.6 3.6.6.6 0 1 .4 1 1V20c0 .6-.4 1-1 1A17 17 0 0 1 3 4c0-.6.4-1 1-1h3.5c.6 0 1 .4 1 1 0 1.3.2 2.5.6 3.6.1.3 0 .7-.2 1z" fill="#777"/></svg>
</div>
<div class="abs phone-num">555 - 014 - 2288</div>
<div class="abs social-top" style="left:930px"></div>
<div class="abs social-top" style="left:973px"></div>
<div class="abs social-top" style="left:1017px"></div>
<div class="abs social-top" style="left:1060px"></div>

<div class="abs nav" style="left:100px">HOME</div>
<div class="abs nav" style="left:195px">BENCH ACTIVITIES</div>
<div class="abs nav" style="left:380px">BENCH EVENTS</div>
<div class="abs nav" style="left:704px">RESOURCES</div>
<div class="abs nav" style="left:850px">ONLINE SHOP</div>
<div class="abs nav" style="left:1007px">CONTACT US</div>

<div class="abs hero" role="img" aria-label="Photo of a maker leaning over a workbench in a wood workshop, using a tablet">
  <h1>RESOURCES</h1>
</div>
<div class="abs logo-disc"><span>The Maple<br>Bench</span></div>

<h2 class="abs script" style="top:462px"><span class="o">Frequently</span> <span class="b">Asked Questions</span></h2>
<p class="abs intro" style="top:539px">Lorem ipsum dolor sit amet, consectetur adipiscing elit, sed do eiusmod tempor incididunt ut labore<br>et dolore magna aliqua. Quis ipsum suspendisse ultrices gravida.</p>

<div class="abs faq" style="top:627px"><span>Finibus Bonorum et Malorum y Cicero in 45 BC</span><svg width="24" height="24"><path d="M12 1v22M1 12h22" stroke="#222" stroke-width="2"/></svg></div>
<div class="abs faq" style="top:696px"><span>Finibus Bonorum et Malorum y Cicero in 45 BC</span><svg width="24" height="24"><path d="M12 1v22M1 12h22" stroke="#222" stroke-width="2"/></svg></div>
<div class="abs faq" style="top:765px"><span>Finibus Bonorum et Malorum y Cicero in 45 BC</span><svg width="24" height="24"><path d="M12 1v22M1 12h22" stroke="#222" stroke-width="2"/></svg></div>
<div class="abs faq" style="top:835px"><span>Finibus Bonorum et Malorum y Cicero in 45 BC</span><svg width="24" height="24"><path d="M12 1v22M1 12h22" stroke="#222" stroke-width="2"/></svg></div>
<div class="abs faq" style="top:904px"><span>Finibus Bonorum et Malorum y Cicero in 45 BC</span><svg width="24" height="24"><path d="M12 1v22M1 12h22" stroke="#222" stroke-width="2"/></svg></div>
<div class="abs faq" style="top:973px"><span>Finibus Bonorum et Malorum y Cicero in 45 BC</span><svg width="24" height="24"><path d="M12 1v22M1 12h22" stroke="#222" stroke-width="2"/></svg></div>

<div class="abs blog-band"></div>
<h2 class="abs script" style="top:1192px"><span class="o">Latest</span> <span class="b">Blog</span></h2>
<p class="abs intro" style="top:1254px">Lorem ipsum dolor sit amet, consectetur adipiscing elit, sed do eiusmod tempor incididunt ut labore<br>et dolore magna aliqua. Quis ipsum suspendisse ultrices gravida.</p>

<div class="abs" style="left:99px;top:1334px;width:641px;height:734px;background:linear-gradient(180deg,#b9b86a 0%,#8a8a78 35%,#6b6a62 65%,#9a968c 100%)" role="img" aria-label="Photo of people building wooden crates in a communal workshop"></div>
<div class="abs kicker" style="left:110px;top:2103px">Read our Blog</div>
<div class="abs post-title" style="left:110px;top:2124px">Lorem ipsum dolor sit amet, consectetur adipiscing</div>
<p class="abs post-text" style="left:110px;top:2164px;width:610px">Lorem ipsum dolor sit amet, cur adipiscing elit, sed do eiusmod tempor incididunt ut labore et dolore magna aliqua.Lorem ipsum dolor sit amet, cur adipiscing elit, sed do eiusmod tempor incididunt ut labore et dolore magna aliqua.Lorem ipsum dolor sit amet, cur adipiscing elit, sed do eiusmod tempor incididunt ut labore et dolore magna aliqua</p>

<div class="abs" style="left:773px;top:1334px;width:323px;height:209px;background:linear-gradient(135deg,#d79a4a 0%,#c9a46a 50%,#8a6a44 100%)" role="img" aria-label="Photo of a handmade wooden chicken coop with straw"></div>
<div class="abs kicker" style="left:773px;top:1567px">Read our Blog</div>
<div class="abs post-title" style="left:773px;top:1588px;width:330px">Sed ut perspiciatis unde omnis iste natus error sit</div>
<p class="abs post-text" style="left:773px;top:1667px;width:325px">Lorem ipsum dolor sit amet, cur adipiscing elit, sed do eiusmod tempor incididunt ut labore et dolore magna aliqua.Lorem ipsr sit amet, cur adipiscing elit, sed do eiusmod tempor incididunt ut labore et dolore magna aliqua.</p>

<div class="abs" style="left:773px;top:1806px;width:323px;height:209px;background:linear-gradient(135deg,#e8e6e2 0%,#8a8c9a 50%,#3a4a7a 100%)" role="img" aria-label="Photo of a family crafting together at a table"></div>
<div class="abs kicker" style="left:773px;top:2039px">Read our Blog</div>
<div class="abs post-title" style="left:773px;top:2060px;width:330px">Sed ut perspiciatis unde omnis iste natus error sit</div>
<p class="abs post-text" style="left:773px;top:2139px;width:325px">Lorem ipsum dolor sit amet, cur adipiscing elit, sed do eiusmod tempor incididunt ut labore et dolore magna aliqua.Lorem ipsr sit amet, cur adipiscing elit, sed do eiusmod tempor incididunt ut labore et dolore magna aliqua.</p>

<h2 class="abs script" style="top:2420px"><span class="o">Free</span> <span class="b">eBooks</span></h2>
<p class="abs intro" style="top:2485px">Lorem ipsum dolor sit amet, consectetur adipiscing elit, sed do eiusmod tempor incididunt ut labore<br>et dolore magna aliqua. Quis ipsum suspendisse ultrices gravida.</p>

<div class="abs book" style="left:99px" role="img" aria-label="eBook cover"></div>
<div class="abs book" style="left:353px" role="img" aria-label="eBook cover"></div>
<div class="abs book" style="left:607px" role="img" aria-label="eBook cover"></div>
<div class="abs book" style="left:862px" role="img" aria-label="eBook cover"></div>
<div class="abs book-name" style="left:99px">Book Name</div>
<div class="abs book-name" style="left:353px">Book Name</div>
<div class="abs book-name" style="left:607px">Book Name</div>
<div class="abs book-name" style="left:862px">Book Name</div>
<div class="abs book-sub" style="left:99px">Sed ut perspiciatis unde</div>
<div class="abs book-sub" style="left:353px">Sed ut perspiciatis unde</div>
<div class="abs book-sub" style="left:607px">Sed ut perspiciatis unde</div>
<div class="abs book-sub" style="left:862px">Sed ut perspiciatis unde</div>

<div class="abs indemnity"></div>
<h2 class="abs script" style="top:3066px;color:var(--white)">Indemnity agreement</h2>
<p class="abs intro" style="top:3133px;color:var(--white)">Lorem ipsum dolor sit amet, consectetur adipiscing elit, sed do eiusmod tempor incididunt ut labore<br>et dolore magna aliqua. Quis ipsum suspendisse ultrices gravida.</p>
<div class="abs btn">DOWNLOAD INDEMNITY AGREEMENT</div>

<div class="abs footer"></div>
<div class="abs f-head" style="left:101px">ABOUT</div>
<div class="abs f-head" style="left:236px">OUR OFFERING</div>
<div class="abs f-head" style="left:421px">OTHER</div>
<div class="abs f-head" style="left:571px">CONTACT US</div>
<div class="abs f-head" style="left:843px">GET UPDATES &amp; PROMOS</div>
<ul class="abs f-list" style="left:101px"><li>Our Story</li><li>Press</li><li>Locations</li><li>Blog</li><li>Contact Us</li></ul>
<ul class="abs f-list" style="left:236px"><li>Projects</li><li>Paint Room</li><li>Parties</li><li>Classes</li></ul>
<ul class="abs f-list" style="left:421px"><li>Franchise</li><li>Gift Cards</li><li>FAQ</li><li>Refund Policy</li></ul>
<ul class="abs f-list" style="left:571px"><li>48 Alder Row Fairbrook USA</li><li>30418</li><li>555 - 014 - 2288</li><li>hello@maplebench.com</li></ul>
<div class="abs email">Email Address</div>
<div class="abs subscribe">SUBSCRIBE</div>
<div class="abs f-social" style="left:852px"></div>
<div class="abs f-social" style="left:893px"></div>
<div class="abs f-social" style="left:935px"></div>
<div class="abs f-social" style="left:978px"></div>
<div class="abs rule"></div>
<div class="abs copy">Copyright © 2021 The Maple Bench. All rights reserved.</div>

</body>
</html>
```